Billboard design 8x3M RAVU (Spanish company)

We´re located in the south of Spain. We run a local telecom company.
We sell Fiber optic, and mobile phone lines mainly.
The billboard will have to be in Spanish, I would like the price to be something you spot on first sight when passing by in the car.
Our company color is blue, like in our logo which I will add. I will also add a example from what we currently have.
The new offer should be:
1000 megas + 100Gigas movil con llamadas ilimitadas. (meaning 1000Mb fiber optic speed and 100Gb data and unlimited calls for 1 mobile line)
Our details are: phone line 958 47 6620
Website: ra-vu.es

```html
<!DOCTYPE html>
<html lang="es">
<head>
<meta charset="utf-8">
<title>RAVU – Valla 8x3</title>
<link rel="stylesheet" href="https://fonts.googleapis.com/css2?family=Barlow+Semi+Condensed:wght@600;700&family=Montserrat:wght@700;800&display=swap">
<style>
  :root {
    --brand-blue: #0c5788;
    --brand-cyan: #12c4f6;
    --white: #ffffff;
    --backdrop: #e9eff4;
  }
  * { margin: 0; padding: 0; box-sizing: border-box; }
  html, body { width: 1200px; height: 874px; overflow: hidden; background: var(--backdrop); }
  .billboard {
    position: absolute; left: 40px; top: 237px;
    width: 1120px; height: 400px; overflow: hidden;
    background: var(--brand-blue);
  }
  .billboard-shapes { position: absolute; inset: 0; }
  .price {
    position: absolute; left: 30px; top: 100px; width: 320px;
    text-align: center; color: var(--brand-blue);
    font-family: "Montserrat", sans-serif; font-weight: 800;
    font-size: 132px; line-height: 1; letter-spacing: -6px; white-space: nowrap;
  }
  .price-label {
    position: absolute; left: 30px; top: 236px; width: 320px;
    text-align: center; color: var(--brand-blue);
    font-family: "Montserrat", sans-serif; font-weight: 800;
    font-size: 36px; line-height: 1; white-space: nowrap;
  }
  .brand {
    position: absolute; left: 600px; top: 12px; width: 320px;
    text-align: center;
  }
  .brand-name {
    font-family: "Montserrat", sans-serif; font-weight: 800;
    font-size: 52px; line-height: 1; color: var(--brand-cyan); letter-spacing: 2px;
  }
  .brand-services {
    margin-top: 6px;
    font-family: "Montserrat", sans-serif; font-weight: 700;
    font-size: 17px; color: var(--white); white-space: nowrap;
  }
  .offer-highlight {
    position: absolute; left: 412px; top: 122px; width: 690px; height: 76px;
    background: var(--brand-cyan); border-radius: 10px;
    display: flex; align-items: center; justify-content: center;
    font-family: "Barlow Semi Condensed", "Arial Narrow", sans-serif; font-weight: 700;
    font-size: 58px; color: var(--white); line-height: 1; white-space: nowrap; overflow: hidden;
  }
  .offer-detail {
    position: absolute; left: 412px; top: 206px; width: 690px;
    text-align: center;
    font-family: "Barlow Semi Condensed", "Arial Narrow", sans-serif; font-weight: 600;
    font-size: 42px; color: var(--white); line-height: 1.1; white-space: nowrap;
  }
  .contact-phone {
    position: absolute; left: 372px; top: 326px;
    display: flex; align-items: center; gap: 12px;
    font-family: "Barlow Semi Condensed", "Arial Narrow", sans-serif; font-weight: 700;
    font-size: 52px; color: var(--brand-blue); line-height: 1; white-space: nowrap;
  }
  .contact-web {
    position: absolute; left: 800px; top: 318px;
    display: flex; align-items: center; gap: 12px;
    font-family: "Montserrat", sans-serif; font-weight: 800;
    font-size: 56px; color: var(--white); line-height: 1; letter-spacing: -1px; white-space: nowrap;
  }
</style>
</head>
<body>
<main class="billboard">
  <svg class="billboard-shapes" viewBox="0 0 1120 400" width="1120" height="400" aria-hidden="true">
    <path d="M0,0 H295 Q465,200 285,400 H0 Z" fill="var(--white)"/>
    <path d="M270,302 H700 C760,302 778,340 792,400 H270 Z" fill="var(--white)"/>
    <path d="M312,0 Q482,200 302,400" fill="none" stroke="var(--white)" stroke-width="4"/>
    <path d="M300,-4 Q470,200 290,404" fill="none" stroke="var(--brand-blue)" stroke-width="6"/>
  </svg>

  <div class="price">35€</div>
  <div class="price-label">POR SÓLO</div>

  <header class="brand">
    <div class="brand-name">RAVU</div>
    <div class="brand-services">Wifi | Fibra | Movil | Tv</div>
  </header>

  <div class="offer-highlight">1000 MEGAS + 100GIGAS</div>
  <div class="offer-detail">MOVIL CON LLAMADAS ILIMITADAS</div>

  <div class="contact-phone">
    <svg width="48" height="48" viewBox="0 0 48 48" aria-hidden="true">
      <circle cx="24" cy="24" r="24" fill="var(--brand-blue)"/>
      <path d="M16 13c2-1 3 0 4 2l2 4c0 1 0 2-1 3l-2 1c1 3 4 6 7 7l1-2c1-1 2-1 3-1l4 2c2 1 3 2 2 4l-1 2c-1 2-3 2-5 2-9-2-15-8-17-17 0-2 0-4 2-5z" fill="var(--white)"/>
    </svg>
    <span>958 47 6620</span>
  </div>

  <div class="contact-web">
    <svg width="52" height="52" viewBox="0 0 52 52" aria-hidden="true">
      <path d="M6 30 L40 16 L28 48 L24 34 Z" fill="var(--white)"/>
      <path d="M36 4v6M46 12l-5 3M44 24l-5-1" stroke="var(--white)" stroke-width="3" stroke-linecap="round"/>
    </svg>
    <span>ra-vu.es</span>
  </div>
</main>
</body>
</html>
```